Bry7Legal Letterhead

Need a new letterhead for my law firm.
IDENTIFYING INFORMATION BELOW:
Anselmo R Quintara III
Attorney at Law
Address: 2847 Larkspur Blvd, Ste 300, Dallas, TX 75204
Phone: 877-482-6017
Fax: 469-738-1452
Email: bry@bry7legal.example
Website: www.bry7legal.example

Colors
0054AA
0677BA
7BADD7
CADEEF
E8F1F8

Requirements
Must have
• Logo needs to be on the letterhead, along with identifying information which is included in the project description.

```html
<!DOCTYPE html>
<html lang="en">
<head>
<meta charset="utf-8">
<title>Bry7Legal Letterhead</title>
<link rel="stylesheet" href="https://fonts.googleapis.com/css2?family=Lato:wght@400;700;900&family=Open+Sans:wght@400;600&display=swap">
<style>
  :root {
    --blue-deep: #0054AA;
    --blue-mid: #0677BA;
    --blue-soft: #7BADD7;
    --blue-pale: #CADEEF;
    --blue-mist: #E8F1F8;
    --ink: #1a1a1a;
    --body: #4a4a4a;
    --paper: #ffffff;
  }
  * { box-sizing: border-box; margin: 0; padding: 0; }
  html, body { width: 1040px; height: 1200px; overflow: hidden; background: var(--paper); }
  .letterhead {
    position: relative; width: 1040px; height: 1200px; background: var(--paper);
    font-family: "Open Sans", Arial, sans-serif; color: var(--body);
  }
  .edge-bar {
    position: absolute; left: 0; top: 0; width: 15px; height: 1200px;
    background: linear-gradient(to bottom, var(--blue-deep), var(--blue-mid) 60%, #1a9bd6);
  }
  .corner-mark {
    position: absolute; left: 0; bottom: 0; width: 76px; height: 68px;
    background: var(--blue-mid);
  }
  .brand {
    position: absolute; left: 97px; top: 44px;
    font-family: "Lato", Arial, sans-serif; font-weight: 900; font-size: 36px;
    letter-spacing: 1px; color: var(--ink);
  }
  .attorney { position: absolute; right: 108px; top: 50px; text-align: right; font-family: "Lato", Arial, sans-serif; }
  .attorney-name { font-size: 21px; font-weight: 700; color: var(--blue-mid); line-height: 1.2; }
  .attorney-title { font-size: 17px; color: var(--ink); line-height: 1.2; }
  .letter { position: absolute; left: 97px; right: 102px; top: 222px; font-size: 15px; }
  .issue-date { margin-bottom: 20px; }
  .recipient { line-height: 18px; margin-bottom: 52px; }
  .salutation { margin-bottom: 26px; }
  .letter-body p { text-align: justify; line-height: 27px; margin-bottom: 27px; }
  .sign-off { position: absolute; left: 97px; top: 818px; font-size: 15px; }
  .signature {
    display: block; margin-top: 14px; width: 240px; height: 26px;
    background: linear-gradient(to right, var(--blue-mist), var(--blue-pale));
  }
  .signer-name { margin-top: 12px; font-size: 18px; font-weight: 600; color: #2e2e2e; }
  .signer-title { margin-top: 6px; font-size: 15px; }
  .footer {
    position: absolute; left: 200px; width: 640px; top: 1114px; text-align: center;
    font-family: "Lato", Arial, sans-serif; font-size: 18px; color: var(--ink);
  }
  .footer-address { padding-bottom: 4px; border-bottom: 1px solid var(--blue-mist); margin: 0 26px 6px; }
  .footer-label { font-weight: 700; color: var(--blue-deep); }
</style>
</head>
<body>
<div class="letterhead">
  <div class="edge-bar"></div>
  <div class="corner-mark"></div>

  <div class="brand">BRY7LEGAL</div>

  <div class="attorney">
    <div class="attorney-name">Anselmo R Quintara III</div>
    <div class="attorney-title">Attorney at Law</div>
  </div>

  <div class="letter">
    <div class="issue-date">Issuing Date: May 5, 2018</div>
    <div class="recipient">
      Name Of Employee Mr. XYZABC<br>
      Address of Employee<br>
      Address Line 2 etc..
    </div>
    <div class="salutation">Dear Mr.XYZABC</div>
    <div class="letter-body">
      <p>Lorem Ipsum has been the industry's standard dummy text ever since the 1500s, when an unknown printer took a galley of type and scrambled it to make a type specimen book. It has survived not only five centuries, but also the leap into electronic typesetting, remaining essentially unchanged. It was popularised in the 1960s with the release of Quillmark sheets containing Lorem Ipsum passages, and more recently with desktop publishing software like Pressleaf Composer including versions of Lorem Ipsum.</p>
      <p>Lorem Ipsum is simply dummy text of the printing and typesetting industry. Lorem Ipsum has been the industry's standard dummy text ever since the 1500s, when an unknown printer took a galley of type and scrambled it to make a type specimen book.</p>
      <p>It has survived not only five centuries, but also the leap into electronic typesetting, remaining essentially unchanged. It was popularised in the 1960s with the release of Quillmark sheets containing Lorem IpsumIpsum passages.</p>
    </div>
  </div>

  <div class="sign-off">
    <div>Yours Sincerely</div>
    <span class="signature" role="img" aria-label="Handwritten signature of Corwin Ashdale"></span>
    <div class="signer-name">Corwin Ashdale</div>
    <div class="signer-title">Managing Director</div>
  </div>

  <div class="footer">
    <div class="footer-address">2847 Larkspur Blvd, Ste 300, Dallas, TX 75204</div>
    <div class="footer-contacts">
      <span class="footer-label">P:</span> 877-482-6017 &nbsp;|&nbsp; <span class="footer-label">F:</span> 469-738-1452 | <span class="footer-label">E:</span> bry@bry7legal.example &nbsp;|&nbsp; <span class="footer-label">W:</span> www.bry7legal.example
    </div>
  </div>
</div>
</body>
</html>
```